Construction Company Facebook Banner

We are a small residential building company, building mostly new homes, renovations, extensions. our social media needs an uplift to look more professional.
I have no photos I wish to use in the banner as of yet however I have included the company logo, and the business card design which has some details.
I would like something simple but professional.
The banner does not need to have email, phone number, services provided etc. all of this is available on the facebook page itself. Something simple and clean please.
Industry/Entity Type
Construction
Requirements
Should not have
- Images of people, QR Code

```html
<!DOCTYPE html>
<html lang="en">
<head>
<meta charset="utf-8">
<title>Residential Builder Cover Banner</title>
<link rel="stylesheet" href="https://fonts.googleapis.com/css2?family=Exo+2:wght@600;700&family=Questrial&display=swap">
<style>
  :root {
    --page-bg: #eef0f3;
    --brand-green: #2fb24c;
    --ring-green: #5cbb7a;
    --ring-light: rgba(255, 255, 255, 0.55);
    --ink: #222222;
    --white: #ffffff;
    --sky: #bcd2e8;
    --house: #6d5b4c;
    --stone: #a9a39a;
    --lawn: #5b8f35;
    --badge-neutral: #d9dde2;
  }
  * { box-sizing: border-box; margin: 0; padding: 0; }
  html, body {
    width: 1200px; height: 851px; overflow: hidden;
    background: var(--page-bg);
  }
  .cover {
    position: absolute; left: 0; top: 183px;
    width: 1200px; height: 485px; overflow: hidden;
  }
  .cover__photo {
    position: absolute; inset: 0;
    background: linear-gradient(180deg,
      var(--sky) 0%, #d9e4ee 16%, var(--house) 34%, #7b6a5a 52%,
      var(--stone) 66%, #7fa252 78%, var(--lawn) 100%);
  }
  .badge-panel {
    position: absolute; left: 733px; top: 2px;
    width: 435px; height: 481px;
  }
  .badge-panel__shape { position: absolute; inset: 0; }
  .badge-panel__content {
    position: absolute; inset: 0;
    display: flex; flex-direction: column; align-items: center;
    text-align: center;
  }
  .contact-phone__icon { margin-top: 40px; width: 36px; height: 36px; }
  .contact-phone__number {
    font-family: "Exo 2", sans-serif; font-weight: 700;
    font-size: 30px; letter-spacing: 1px; color: var(--ink);
    line-height: 1; margin-top: 2px;
  }
  .tagline {
    font-family: "Exo 2", sans-serif; font-weight: 600;
    font-size: 27px; line-height: 28px; color: var(--brand-green);
    margin-top: 16px; width: 360px;
  }
  .intro {
    font-family: "Questrial", sans-serif;
    font-size: 18px; line-height: 28px; color: var(--ink);
    margin-top: 10px; width: 370px; letter-spacing: 0.3px;
  }
  .licence-box {
    margin-top: 8px; width: 360px; height: 68px;
    background: var(--brand-green); border-radius: 3px;
    color: var(--white); font-family: "Questrial", sans-serif;
    display: flex; flex-direction: column; justify-content: center;
  }
  .licence-box__title { font-size: 22px; line-height: 26px; }
  .licence-box__ids { font-size: 16px; line-height: 22px; letter-spacing: 0.3px; }
  .member-badge {
    margin-top: 10px; width: 112px; height: 74px;
    background: var(--badge-neutral); border-radius: 4px;
  }
</style>
</head>
<body>
  <section class="cover">
    <div class="cover__photo" role="img" aria-label="Photo of a new single-storey home with stone base, timber gables, front porch and green lawn"></div>

    <div class="badge-panel">
      <svg class="badge-panel__shape" viewBox="0 0 435 481" aria-hidden="true">
        <polygon points="217.5,6 429,118 429,363 217.5,475 6,363 6,118"
          fill="var(--ring-light)" stroke="var(--ring-light)" stroke-width="12" stroke-linejoin="round"/>
        <polygon points="217.5,22 412,126 412,355 217.5,459 23,355 23,126"
          fill="var(--white)" stroke="var(--ring-green)" stroke-width="12" stroke-linejoin="round"/>
      </svg>

      <div class="badge-panel__content">
        <svg class="contact-phone__icon" viewBox="0 0 24 24" fill="none" stroke="#111" stroke-width="1.4" stroke-linecap="round" stroke-linejoin="round" aria-hidden="true">
          <path d="M5 3h3l1.5 4.5-2 1.3a11 11 0 0 0 7.7 7.7l1.3-2L21 16v3a2 2 0 0 1-2 2A17 17 0 0 1 3 5a2 2 0 0 1 2-2z"/>
          <path d="M14 3.5a7 7 0 0 1 6.5 6.5M14 7a3.5 3.5 0 0 1 3 3"/>
        </svg>
        <p class="contact-phone__number">0400 123 987</p>
        <h2 class="tagline">Creating Spaces You’ll Love to Live In</h2>
        <p class="intro">We Are A Small Residential Building Company, Building Mostly New Homes, Renovations, Extensions</p>
        <div class="licence-box">
          <p class="licence-box__title">Fully Licensed and Insured</p>
          <p class="licence-box__ids">ABN: 12 345 678 901 | QBCC: 765 4321</p>
        </div>
        <div class="member-badge" role="img" aria-label="Industry association membership badge"></div>
      </div>
    </div>
  </section>
</body>
</html>
```